QRV Advisors needs a web site

We need a web site for www.qrvadvisors-example.com. QRV is a mergers and acquisition consulting company that focuses our buyer and seller services on logistics companies. We help put companies together, and help with legal and financial due diligence. We want the web site to express our service and show the logistics components. We want personalized images versus pictures of trucks and airplanes.

Our new logo uses Burgandy and grey colors. Image attached. We are not in to bold, big letters...classy, artistic, low key preferred. Confidentiality, experience, professional are what we want to express on the site.

All we expect for the first part of this project is a home page, and one subpage.  We are budgeting other funds for the technical aspects of the web site

Reason: All that I'm seeing so far is trucks, forklifts and planes. We are a legal mergers and acquisitions firm that focus on logistics. I like some of the images to say logistics, but really want it say legal, financial, and putting companies together. Will pay extra for the sub page if someone can impress us with a home page.

Reason: Swamped with another project at the moment...will work on this over the weekend and provide designer feedback and select final design by Tuesday

```html
<!DOCTYPE html>
<html lang="en">
<head>
<meta charset="utf-8">
<title>QRV Advisors — Mergers and Acquisition Consulting</title>
<link href="https://fonts.googleapis.com/css2?family=Open+Sans:wght@400;600;700&family=Oswald:wght@400;500;700&display=swap" rel="stylesheet">
<style>
:root{
  --brand:#a51b2d;
  --accent:#cf0b44;
  --dark:#3a3939;
  --darker:#2b2a2a;
  --topbar:#4b4849;
  --ink:#222;
  --body:#444;
  --muted:#777;
  --hero:#eceef3;
  --band:#efefef;
  --line:#ddd;
  --white:#fff;
}
*{box-sizing:border-box;margin:0;padding:0}
html,body{width:926px;height:1200px;overflow:hidden;background:var(--white)}
body{font-family:"Open Sans",Arial,sans-serif;color:var(--body);position:relative}
.abs{position:absolute}

/* top bar */
.topbar{left:0;top:0;width:926px;height:18px;background:var(--topbar);color:#eee;font-size:9px}
.topbar .call{left:553px;top:3px;display:flex;gap:5px;align-items:center}
.topbar .mail{left:662px;top:3px;display:flex;gap:5px;align-items:center}

/* header */
.header{left:0;top:18px;width:926px;height:65px;background:var(--white);border-bottom:2px solid var(--brand)}
.logo{left:110px;top:19px;display:flex;align-items:center;gap:7px;color:var(--brand);font-size:17px;font-weight:600;letter-spacing:.5px}
.logo .dot{width:10px;height:10px;background:var(--brand);border-radius:50%}
.nav{left:342px;top:31px;display:flex;height:34px}
.nav a{display:flex;align-items:center;padding:0 11px;background:var(--brand);color:#fff;font-size:9.5px;text-decoration:none;border-right:1px solid #8c1424;letter-spacing:.2px}
.nav a:first-child{background:#5a5758;border-radius:3px 0 0 0;padding:0 14px}
.nav a:last-child{border-radius:0 3px 0 0;border-right:none}

/* hero */
.hero{left:0;top:85px;width:926px;height:325px;background:var(--hero);border-bottom:3px solid var(--brand)}
.hero-photo{left:464px;top:0;width:462px;height:322px;background:linear-gradient(110deg,var(--hero) 0%,#8da2c8 14%,#3c5a8f 45%,#23345a 75%,#1a2440 100%)}
.hero .kicker{left:120px;top:40px;font-family:Oswald,sans-serif;font-size:21px;color:#555;font-weight:400}
.hero .kicker b{color:var(--brand);font-weight:400}
.hero h1{left:120px;top:68px;font-family:Oswald,sans-serif;font-size:30px;font-weight:700;color:var(--brand);letter-spacing:.3px}
.hero h2{left:126px;top:123px;width:320px;font-size:14px;font-weight:600;color:#222;line-height:20px}
.hero p{left:126px;top:175px;width:290px;font-size:11.8px;line-height:18.5px;color:#555}
.btn-learn{left:126px;top:247px;width:112px;height:28px;border-radius:14px;background:linear-gradient(#d43a3f,#a01720);color:#fff;font-size:12px;display:flex;align-items:center;justify-content:center;box-shadow:0 0 0 3px #fff,0 2px 4px rgba(0,0,0,.3)}
.dots{left:128px;top:297px;display:flex;gap:5px}
.dots span{width:12px;height:12px;border-radius:50%;background:#fff;border:1px solid #ccc}
.dots span.on{background:var(--brand);box-shadow:inset 0 0 0 2px #fff}

/* welcome */
.welcome{left:0;top:436px;width:926px;text-align:center}
.welcome h3{font-size:22px;font-weight:400;color:#111}
.welcome h3 span{color:var(--accent)}
.welcome p{margin:7px auto 0;width:670px;font-size:10.3px;line-height:16.2px;color:#444}

/* services */
.services{left:0;top:558px;width:926px;height:304px;background:var(--band)}
.card{top:22px;width:228px;height:250px;background:#fff;border:1px solid #e2e2e2;box-shadow:0 10px 8px -8px rgba(0,0,0,.25)}
.card h4{height:30px;padding:5px 13px;font-size:16px;font-weight:400;color:#222;border-bottom:1px solid #e8e8e8;box-shadow:0 2px 3px rgba(0,0,0,.08)}
.card h4 span{color:var(--accent)}
.card .photo{margin:15px 11px 0;height:97px;border:1px solid #ccc}
.card p{margin:6px 10px 0;font-size:9.6px;line-height:14.8px;color:#444}
.card .more{position:absolute;right:10px;bottom:8px;background:var(--accent);color:#fff;font-size:8.5px;font-weight:700;padding:1px 5px;line-height:13px}

/* news */
.news-title{left:110px;top:886px;font-size:18px;color:#222}
.news-title span{color:var(--accent)}
.news-dots{left:771px;top:902px;display:flex;gap:3px}
.news-dots span{width:7px;height:7px;border-radius:50%;background:#ccc}
.news-dots span.on{background:var(--accent)}
.news-rule{left:108px;top:919px;width:708px;border-top:1px dotted #aaa}
.news-item{top:932px;width:230px;height:60px;display:flex;gap:10px}
.news-item.sep{border-left:1px solid #e2e2e2;padding-left:16px}
.cal{width:26px;text-align:center;flex:none}
.cal .box{height:24px;border:2px solid #999;border-top-width:4px;border-radius:2px;font-size:10px;color:var(--accent);line-height:18px}
.cal .m{font-size:8.5px;font-weight:700;color:#555;margin-top:1px}
.news-item h5{font-size:10.5px;font-weight:400;color:var(--accent);margin-bottom:2px}
.news-item p{font-size:9.1px;line-height:11.5px;color:#333}

/* footer */
.footer{left:0;top:1017px;width:926px;height:149px;background:var(--dark);border-top:3px solid var(--darker);color:#eee}
.fnav{left:110px;top:18px;display:flex;gap:19px;font-size:10px}
.map{left:108px;top:51px;width:156px;height:77px;background:linear-gradient(135deg,#e9e3d4,#d7cdb4 60%,#c9b89a)}
.loc{left:272px;top:51px;font-size:10px;line-height:18.6px}
.loc .lbl,.tel .lbl{font-weight:600}
.loc svg,.tel svg{position:absolute;left:0;top:3px}
.loc div,.tel div{padding-left:18px}
.tel{left:396px;top:54px;font-size:10px;line-height:19px;letter-spacing:.5px}
.nl-title{left:518px;top:16px;font-size:21px;font-weight:400}
.nl-text{left:518px;top:52px;width:130px;font-size:9.8px;line-height:13.5px}
.nl-form{left:650px;top:21px;width:167px;height:92px;background:#6a6a6a;padding:7px 8px}
.nl-form .field{height:19px;background:#fff;color:#333;font-size:9.5px;padding:2px 5px;margin-bottom:8px}
.nl-form .sub{width:65px;height:20px;background:var(--accent);color:#fff;font-size:11.5px;font-weight:700;display:flex;align-items:center;justify-content:center;border-radius:2px}
.bottombar{left:0;top:1166px;width:926px;height:34px;background:#555;color:#ccc;font-size:9.8px}
.bottombar .copy{left:114px;top:11px}
.social{right:112px;top:10px;display:flex;gap:12px}
.social span{width:14px;height:14px;border-radius:50%;background:#eee}
</style>
</head>
<body>

<div class="abs topbar">
  <div class="abs call">
    <svg width="10" height="10" viewBox="0 0 10 10"><path d="M2 0.5 L3.5 2.5 L2.6 3.6 Q3.8 6.2 6.4 7.4 L7.5 6.5 L9.5 8 L8.4 9.5 Q2 8.8 0.5 2 Z" fill="#ccc"/></svg>
    Call: 123-456-7890
  </div>
  <div class="abs mail">
    <svg width="12" height="9" viewBox="0 0 12 9"><rect x="0.5" y="0.5" width="11" height="8" fill="#bbb"/><path d="M0.5 0.5 L6 5 L11.5 0.5" fill="none" stroke="#666"/></svg>
    info@qrvadvisors-example.com
  </div>
</div>

<header class="abs header">
  <div class="abs logo"><span class="dot"></span>QRV Advisors</div>
  <nav class="abs nav">
    <a>HOME</a><a>ABOUT</a><a>CONSULTING SERVICES</a><a>NEWS &amp; EVENTS</a><a>FAQ'S</a><a>CONTACT</a>
  </nav>
</header>

<section class="abs hero">
  <div class="abs hero-photo" role="img" aria-label="Two business partners shaking hands in front of a glass office tower"></div>
  <div class="abs kicker"><b>QRV</b> is Mergers And Acquisition</div>
  <h1 class="abs">CONSULTING COMPANY</h1>
  <h2 class="abs">We Offer Business Planning ,Merger And Acquisition(M&amp;A) Advisory Services.</h2>
  <p class="abs">Lorem ipsum dolor sit amet, consectetuer in a to adipiscing elit,Sed diam nonummy nibhaops adip euismod tincidunt ut laoreet dolore magnad.</p>
  <div class="abs btn-learn">LEARN MORE</div>
  <div class="abs dots"><span class="on"></span><span></span><span></span><span></span></div>
</section>

<section class="abs welcome">
  <h3>Welcome To <span>&nbsp;QRV Advisors</span></h3>
  <p>QRV assists business owners within the logistics industry to implement growth and exit strategies.QRV services are offered by industry executives with extensive M&amp;A experience. Your company will benefit from a unique and outside perspective from consultants that understand your business.QRV can help you formulate and execute your growth strategy. We take a strategic and consultative approach with our advisory services that will help you grow your business effectively.</p>
</section>

<section class="abs services">
  <article class="abs card" style="left:108px">
    <h4>Business <span>Planning</span></h4>
    <div class="photo" role="img" aria-label="Team gathered around a laptop in a meeting" style="background:linear-gradient(#eceff2,#c9cdd2)"></div>
    <p>Lorem ipsum dolor sit amet, consectetuer in adipiscing elit,Sed diam nonummy nibhaops euismod tincidunt ut laoreet dolore magnad aliquam erat volutpat. Ut wisi enim adminio veniam, quis nostrud exerci tationdada .</p>
    <span class="more">Learn more »</span>
  </article>
  <article class="abs card" style="left:348px">
    <h4>Business <span>Merger</span></h4>
    <div class="photo" role="img" aria-label="Handshake against a blue sky and office towers" style="background:linear-gradient(#1d3e7a,#6b8cc4 55%,#b7c6dc)"></div>
    <p>Lorem ipsum dolor sit amet, consectetuer in adipiscing elit,Sed diam nonummy nibhaops euismod tincidunt ut laoreet dolore magnad aliquam erat volutpat. Ut wisi enim adminio veniam, quis nostrud exerci tationdada .</p>
    <span class="more">Learn more »</span>
  </article>
  <article class="abs card" style="left:588px">
    <h4>Acquisition <span>(M&amp;A) Advisory</span></h4>
    <div class="photo" role="img" aria-label="Advisor reviewing a document with a couple" style="background:linear-gradient(90deg,#3b3e48,#8e8a86 50%,#c8b6a4)"></div>
    <p>Lorem ipsum dolor sit amet, consectetuer in adipiscing elit,Sed diam nonummy nibhaops euismod tincidunt ut laoreet dolore magnad aliquam erat volutpat. Ut wisi enim adminio veniam, quis nostrud exerci tationdada .</p>
    <span class="more">Learn more »</span>
  </article>
</section>

<h3 class="abs news-title" style="font-weight:400">Latest <span>News</span></h3>
<div class="abs news-dots"><span class="on"></span><span></span><span></span><span></span></div>
<div class="abs news-rule"></div>
<article class="abs news-item" style="left:109px">
  <div class="cal"><div class="box">10</div><div class="m">FEB</div></div>
  <div><h5>Lorem ipsum dolor sit amet</h5><p>Lorem ipsum dolor sit amet, in to adips consectetit uer adipiscing elit, sed diam nonummy oll euismod tincidunt aliquam.</p></div>
</article>
<article class="abs news-item sep" style="left:340px">
  <div class="cal"><div class="box">10</div><div class="m">FEB</div></div>
  <div><h5>Lorem ipsum dolor sit amet</h5><p>Lorem ipsum dolor sit amet, in to adips consectetit uer adipiscing elit, sed diam nonummy oll euismod tincidunt aliquam.</p></div>
</article>
<article class="abs news-item sep" style="left:586px">
  <div class="cal"><div class="box">10</div><div class="m">FEB</div></div>
  <div><h5>Lorem ipsum dolor sit amet</h5><p>Lorem ipsum dolor sit amet, in to adips consectetit uer adipiscing elit, sed diam nonummy oll euismod tincidunt aliquam.</p></div>
</article>

<footer class="abs footer">
  <nav class="abs fnav"><span>Home</span><span>About</span><span>Consulting Services</span><span>News &amp; Events</span><span>Faq's</span><span>Contact</span></nav>
  <div class="abs map" role="img" aria-label="Street map of the main office location"></div>
  <div class="abs loc">
    <svg width="9" height="12" viewBox="0 0 9 12"><path d="M4.5 11.5 L1 5.5 A3.6 3.6 0 1 1 8 5.5 Z" fill="none" stroke="#bbb" stroke-width="1.4"/><circle cx="4.5" cy="4.3" r="1.3" fill="#bbb"/></svg>
    <div class="lbl">Location</div>
    <div>Main office Location,</div>
    <div>Lane no. Po box 123</div>
    <div>City, Zip 0000123</div>
  </div>
  <div class="abs tel">
    <svg width="10" height="11" viewBox="0 0 10 10"><path d="M2 0.5 L3.5 2.5 L2.6 3.6 Q3.8 6.2 6.4 7.4 L7.5 6.5 L9.5 8 L8.4 9.5 Q2 8.8 0.5 2 Z" fill="#bbb"/></svg>
    <div class="lbl">Phone:</div>
    <div>123-456-7890</div>
    <div class="lbl">FAX:</div>
    <div>123-456-7890</div>
  </div>
  <h3 class="abs nl-title">Newsletter</h3>
  <p class="abs nl-text">Get Valuable Tips and News from QRV, Signup to our Monthly Newsletter today!</p>
  <form class="abs nl-form">
    <div class="field">Name</div>
    <div class="field">Email</div>
    <div class="sub">Subscribe</div>
  </form>
</footer>

<div class="abs bottombar">
  <div class="abs copy">© Copyright 2013 QRV Advisors.</div>
  <div class="abs social" aria-label="Social media links"><span></span><span></span><span></span></div>
</div>

</body>
</html>
```